Bicycle dealer and service & repair center

The registered brand of our company, Rad Lindhof, means bicycle of the city Zurich (Switzerland) and is the largest dealer of e-bikes, folding bikes and cargo bikes in Switzerland. Rad Lindhof also sells a substantial amount of road bikes, mountainbikes, trailers and bicycles without electric motor. The more, we are known for special bikes (tandems, Swiss military bicycles, postman bicycles, and others).Rad Lindhof has around 10 highly skilled employees and runs a well-equipped service & repair center. We have around 50 brand dealerships for replacement parts, diagnostic devices and are proud about our after-sales service.Our website is fully functional (see www.rad-lindhof.ch) and available in three languages (DE, EN, FR for the french speaking part of Switzerland). Live stock information is provided by https://www.rad-lindhof.ch/en/rad.We need a redesign of our website. The focus should be on:- e-catalog with simple search and extended search - e-commerce (e.g. add to chart, favorites, text search, filter, sort, related products, similar products, most popular search, related articles, top listings, promotions...)- cross-selling with our affiliated company Rad Brunnegg, our bicycle shop in a city nearby Zurich.- service and repair- company (sustainable business, emission-free mobility, public relation, well-trained and friendly staff)- mobile friendlyness- maximize usability- maximize usage of display for useful information- easy to find relevant information- simple search functionalityKey audience is:- middle to high-price bicycle customers- existing and returning clients- prospective employees- members of the pressThe goal of the website and its redesign is:- increase the number of enquiries via website- increase online sales- share information with others (addtoany)- provide information about the right selection of bicycle (faq, detailed information about components) to reduce the admin associated with new enquiries- highlight special offers (e.g. free bicycle service slots, sunday exhibition)As Rad Lindhof has many returning customers and already high website traffic (according to SERP), the new design should be a smooth transition from the existing website.Websites we like:- https://tramofix.ch/- https://www.kurbelhaus.ch/- https://www.quandor.ch/- https://www.autoscout24.ch/deGood luck and have fun creating our new design!
Updates

website we also like: https://www.pedalora.ch/

Target Market(s)

Urban bicycle riders

Industry/Entity Type

Retail

Coding

Coded - Design and coding required

Number of Pages Required

5+ page

Font styles to use
Other font styles liked:
• Avenir (https://www.glyphbazar.com/fonts/typecraft/avenir/)

Colors

Designer to choose colors to be used in the design.

Requirements
Must have
• The actual content www.rad-lindhof.ch must be published with the new website design. Additional content should be added according to project description (see above).
Nice to have
• - we use the font type Avenir (https://www.glyphbazar.com/fonts/typecraft/avenir/) for business cards, leaflets etc
Should not have
• Frippery

```html
<!DOCTYPE html>
<html lang="en">
<head>
<meta charset="utf-8">
<title>Rad Lindhof – E-Bikes, Velos, Service</title>
<link href="https://fonts.googleapis.com/css2?family=Nunito+Sans:wght@400;600;700;800&display=swap" rel="stylesheet">
<style>
:root{
  --dark:#2d2d2f;
  --footer:#1e1e22;
  --green:#6fae1f;
  --blue:#1b74b0;
  --orange:#f39c12;
  --text:#222;
  --muted:#8a8a8a;
  --line:#dcdcdc;
  --band:#efefef;
}
*{box-sizing:border-box;margin:0;padding:0}
html,body{width:1200px;height:2630px;overflow:hidden}
body{position:relative;font-family:"Nunito Sans",Arial,sans-serif;color:var(--text);background:#fff}
ul{list-style:none}

/* header */
.site-header{position:absolute;left:0;top:0;width:1200px;height:91px;background:var(--dark);color:#fff}
.brand-name{position:absolute;left:99px;top:14px;width:226px;font-size:34px;font-weight:800;letter-spacing:-1px;line-height:1;white-space:nowrap}
.brand-mark{position:absolute;left:331px;top:9px;width:68px;height:68px;background:var(--blue);border-radius:8px}
.brand-tag{position:absolute;left:100px;top:62px;width:226px;font-size:8.6px;color:#fff;white-space:nowrap}
.search{position:absolute;left:493px;top:12px;display:flex;height:31px}
.search input{width:182px;border:0;padding:0 14px;font:13px "Nunito Sans",sans-serif;border-radius:3px 0 0 3px}
.search .cat{width:138px;background:#fff;border-left:1px solid #ddd;font-size:12.5px;color:#555;padding:7px 12px;display:flex;justify-content:space-between}
.search button{width:51px;border:0;background:var(--blue);border-radius:0 3px 3px 0}
.util{position:absolute;top:19px;font-size:13px;display:flex;align-items:center;gap:6px;white-space:nowrap}
.count{background:var(--green);font-size:10px;font-weight:700;padding:0 4px;border-radius:2px}
.nav-link{position:absolute;top:62px;font-size:14.5px;white-space:nowrap}
.cart{position:absolute;top:63px;left:1018px;font-size:13px;display:flex;gap:6px;align-items:center;white-space:nowrap}

/* hero */
.categories{position:absolute;left:97px;top:91px;width:232px;height:405px;box-shadow:0 1px 4px rgba(0,0,0,.15)}
.categories h2{background:var(--green);color:#fff;font-size:18px;font-weight:600;height:44px;line-height:44px;padding-left:13px}
.categories li{height:39.5px;border-bottom:1px solid #e6e6e6;display:flex;justify-content:space-between;align-items:center;padding:0 14px;font-size:15.5px;color:#333}
.hero{position:absolute;left:337px;top:91px;width:751px;height:405px;background:linear-gradient(160deg,#5a83b7 0%,#9bb2c9 38%,#c9c6b2 55%,#6b6a45 80%,#3d3b24 100%)}
.hero h1{position:absolute;right:70px;top:50px;color:#fff;font-size:48px;font-weight:800}
.dots{display:flex;gap:7px;justify-content:center}
.dots i{width:8px;height:8px;border-radius:50%;border:1.5px solid #888}
.dots i.on{background:#666;border-color:#666}
.hero .dots{position:absolute;right:52px;bottom:25px}
.hero .dots i{border-color:#fff}.hero .dots i.on{background:#fff}

/* product panels */
.products{position:absolute;left:90px;width:1003px;height:364px;border:1px solid var(--line)}
.products header{height:66px;border-bottom:1px solid var(--line);display:flex;justify-content:space-between;align-items:center;padding:0 38px 0 34px}
.products h2{font-size:33px;font-weight:600}
.sort{display:flex;align-items:center;gap:12px;font-size:15px;color:#555;text-decoration:underline}
.sort b{width:27px;height:25px;background:#d5d5d5;display:flex;align-items:center;justify-content:center;font-size:11px;text-decoration:none}
.grid{display:flex;height:257px;border-bottom:1px solid var(--line)}
.card{border-right:1px solid var(--line);position:relative;text-align:center}
.card:last-child{border-right:0}
.pic{position:absolute;top:14px;left:50%;transform:translateX(-50%);width:196px;height:136px;background:radial-gradient(ellipse at center,#e9ecef 0%,#fff 72%)}
.badge{position:absolute;top:26px;left:22px;background:var(--orange);color:#fff;font-size:9px;font-weight:700;padding:2px 7px;border-radius:9px}
.card h3{position:absolute;top:180px;width:100%;font-size:18px;font-weight:400}
.price{position:absolute;top:214px;width:100%;font-size:14px}
.price s{color:var(--muted);margin-right:10px}
.products .dots{margin-top:17px}

/* services */
.services-title{position:absolute;left:105px;top:1482px;font-size:35px;font-weight:400}
.service{position:absolute;top:1562px;width:304px}
.service .photo{height:189px}
.service h3{margin:38px 0 0 4px;font-size:22px;font-weight:400;line-height:24px;color:#333}
.service p{margin:14px 0 0 1px;font-size:16.3px;line-height:26px;color:#333}
.btn{display:inline-block;margin-top:19px;width:152px;height:44px;border:2px solid #222;border-radius:23px;text-align:center;line-height:40px;font-size:15px;font-weight:600}

/* newsletter */
.newsletter{position:absolute;left:0;top:2037px;width:1200px;height:138px;background:var(--band);text-align:center}
.newsletter h2{margin-top:40px;font-size:21px;font-weight:400}
.nl-form{display:flex;justify-content:center;gap:9px;margin-top:17px}
.nl-form span{width:291px;height:36px;background:#fff;border:1px solid #ccc;text-align:left;padding:9px 0 0 36px;font-size:12.5px;color:#777;position:relative}
.nl-form span:before{content:"";position:absolute;left:13px;top:13px;width:13px;height:9px;background:#888}
.nl-form button{width:137px;height:35px;background:var(--blue);color:#fff;border:0;font:700 13px "Nunito Sans",sans-serif}

/* footer */
.site-footer{position:absolute;left:0;top:2175px;width:1200px;height:455px;background:var(--footer);color:#fff}
.fcol{position:absolute}
.fcol h4{font-size:16px;font-weight:400;color:#a0a0a6;margin-bottom:9px}
.fcol li{font-size:11.5px;line-height:25.8px;white-space:nowrap}
.copyright{position:absolute;left:99px;top:2597px;font-size:12.5px;color:#fff}
.connect{position:absolute;left:797px;top:2584px;display:flex;align-items:center;gap:9px;color:#fff;font-size:15px}
.connect span{margin-right:19px}
.connect b{width:34px;height:34px;display:block}
</style>
</head>
<body>

<header class="site-header">
  <span class="brand-name">RAD LINDHOF</span>
  <span class="brand-mark"></span>
  <div class="brand-tag">E-Bikes | Cargobikes | Velos | Service &amp; Reparaturen</div>
  <div class="search">
    <input placeholder="Search...">
    <div class="cat">All Categories <span>▾</span></div>
    <button aria-label="Search"><svg width="15" height="15" viewBox="0 0 16 16"><circle cx="6.5" cy="6.5" r="5" fill="none" stroke="#fff" stroke-width="2"/><path d="M10.5 10.5 15 15" stroke="#fff" stroke-width="2"/></svg></button>
  </div>
  <div class="util" style="left:879px"><svg width="14" height="13" viewBox="0 0 14 13"><path d="M7 12 1.5 6.5A3.3 3.3 0 0 1 7 2.3a3.3 3.3 0 0 1 5.5 4.2z" fill="#fff"/></svg>Wishlist <span class="count">27</span></div>
  <div class="util" style="left:987px"><svg width="13" height="13" viewBox="0 0 13 13"><circle cx="6.5" cy="4" r="3.2" fill="#fff"/><path d="M0 13c0-4 3-5.5 6.5-5.5S13 9 13 13z" fill="#fff"/></svg>My Account <span style="color:var(--green);font-size:10px">▼</span></div>
  <nav>
    <span class="nav-link" style="left:675px">Velos</span>
    <span class="nav-link" style="left:735px">News</span>
    <span class="nav-link" style="left:796px">Services</span>
    <span class="nav-link" style="left:872px">About Us</span>
    <span class="nav-link" style="left:956px">FAQ</span>
  </nav>
  <div class="cart"><svg width="15" height="13" viewBox="0 0 15 13"><path d="M0 1h3l2 8h8l2-6H4" fill="none" stroke="#fff" stroke-width="1.6"/><circle cx="6" cy="11.5" r="1.3" fill="#fff"/><circle cx="12" cy="11.5" r="1.3" fill="#fff"/></svg>Cart <span class="count">4</span></div>
</header>

<aside class="categories">
  <h2>Shop by Category</h2>
  <ul>
    <li>Racing Bikes<span>›</span></li><li>City Bikes<span>›</span></li><li>Tour Bike<span>›</span></li>
    <li>Ebikes<span>›</span></li><li>Electric Bikes<span>›</span></li><li>Accessories<span>›</span></li>
    <li>Bike Repair<span>›</span></li><li>Bicycle Service<span>›</span></li><li>Parts<span>›</span></li>
  </ul>
</aside>
<section class="hero" role="img" aria-label="Mountain biker riding across a hilltop at sunrise">
  <h1>E-Bikes</h1>
  <div class="dots"><i></i><i class="on"></i><i></i><i></i><i></i></div>
</section>

<section class="products" style="top:575px">
  <header><h2>Related Products</h2><div class="sort">Sort by: <b>▼</b></div></header>
  <div class="grid">
    <div class="card" style="width:244px"><div class="pic" role="img" aria-label="Dark mountain bike"></div><span class="badge">27% OFF</span><h3>Mountain Bikes</h3><p class="price"><s>$228.90</s>$260.90</p></div>
    <div class="card" style="width:257px"><div class="pic" role="img" aria-label="Black road e-bike"></div><span class="badge">50% OFF</span><h3>Ebikes</h3><p class="price"><s>$240.50</s>$120.00</p></div>
    <div class="card" style="width:257px"><div class="pic" role="img" aria-label="Black city bike with purple rims"></div><span class="badge">40% OFF</span><h3>City Bikes</h3><p class="price"><s>$799.90</s>$478.90</p></div>
    <div class="card" style="width:243px"><div class="pic" role="img" aria-label="Blue touring road bike"></div><span class="badge">75% OFF</span><h3>Tour Bike</h3><p class="price"><s>$1000.00</s>$250.00</p></div>
  </div>
  <div class="dots"><i></i><i class="on"></i><i></i><i></i><i></i></div>
</section>

<section class="products" style="top:987px">
  <header><h2>Similar Products</h2><div class="sort">Sort by: <b>▼</b></div></header>
  <div class="grid">
    <div class="card" style="width:244px"><div class="pic" role="img" aria-label="Dark mountain bike"></div><span class="badge">27% OFF</span><h3>Mountain Bikes</h3><p class="price"><s>$228.90</s>$260.90</p></div>
    <div class="card" style="width:257px"><div class="pic" role="img" aria-label="Black road e-bike"></div><span class="badge">50% OFF</span><h3>Ebikes</h3><p class="price"><s>$240.50</s>$120.00</p></div>
    <div class="card" style="width:257px"><div class="pic" role="img" aria-label="Black city bike with purple rims"></div><span class="badge">40% OFF</span><h3>City Bikes</h3><p class="price"><s>$799.90</s>$478.90</p></div>
    <div class="card" style="width:243px"><div class="pic" role="img" aria-label="Blue touring road bike"></div><span class="badge">75% OFF</span><h3>Tour Bike</h3><p class="price"><s>$1000.00</s>$250.00</p></div>
  </div>
  <div class="dots"><i></i><i class="on"></i><i></i><i></i><i></i></div>
</section>

<h2 class="services-title">Our Services</h2>
<article class="service" style="left:105px">
  <div class="photo" role="img" aria-label="Cyclist on a mountain trail below rocky peaks" style="background:linear-gradient(180deg,#6fa0d8 0%,#b9c3c8 35%,#7c7a58 60%,#c59a48 100%)"></div>
  <h3>At vero eos et<br>accusamus et iusto odio</h3>
  <p>Lorem ipsum dolor sit amet, consectetur adipiscing elit, sed do eiusmod tempor incididunt ut labore et</p>
  <span class="btn">READ MORE</span>
</article>
<article class="service" style="left:440px">
  <div class="photo" role="img" aria-label="Cyclist racing down a mountain road" style="background:linear-gradient(180deg,#3f7fb8 0%,#8eb0c2 30%,#4e5b3c 60%,#6c6c6c 100%)"></div>
  <h3>At vero eos et<br>accusamus et iusto odio</h3>
  <p>Lorem ipsum dolor sit amet, consectetur adipiscing elit, sed do eiusmod tempor incididunt ut labore et</p>
  <span class="btn">READ MORE</span>
</article>
<article class="service" style="left:777px">
  <div class="photo" role="img" aria-label="Mountain biker on rocky terrain above a valley" style="background:linear-gradient(180deg,#8d9aa8 0%,#6c8597 40%,#55595a 70%,#3b3a37 100%)"></div>
  <h3>At vero eos et<br>accusamus et iusto odio</h3>
  <p>Lorem ipsum dolor sit amet, consectetur adipiscing elit, sed do eiusmod tempor incididunt ut labore et</p>
  <span class="btn">READ MORE</span>
</article>

<section class="newsletter">
  <h2>Subscribe to your Newsletter</h2>
  <div class="nl-form"><span>Your e-mail</span><button>GET STARTED</button></div>
</section>

<footer class="site-footer">
  <div class="fcol" style="left:101px;top:40px"><h4>Buy</h4><ul><li>Registration</li><li>Money Back Guarantee</li><li>Bidding &amp; buying help</li><li>Stores</li><li>Local</li><li>guides</li></ul></div>
  <div class="fcol" style="left:307px;top:43px"><h4>Sell</h4><ul><li>Start selling</li><li>Learn to sell</li><li>Business sellers</li><li>Affiliates</li></ul>
    <h4 style="margin-top:26px">Tools &amp; apps</h4><ul><li>Mobile apps</li><li>Downloads</li><li>Developers</li><li>Security center</li><li>official time</li><li>Site map</li></ul></div>
  <div class="fcol" style="left:483px;top:40px"><h4>Rad-Lindhof Companies</h4><ul><li>Rad-Lindhof Classifieds</li><li>TicketHall</li><li>NearSix</li><li>See all companies</li></ul>
    <h4 style="margin-top:30px">Stay connected</h4><ul><li>Rad-Lindhof Blogs</li><li>Pedalbook</li><li>Chirper</li><li>Circles+</li></ul></div>
  <div class="fcol" style="left:711px;top:40px"><h4>About Rad-Lindhof</h4><ul><li>Company info</li><li>News</li><li>Investors</li><li>Careers</li><li>Government relations</li><li>Advertise with us</li><li>Policies</li><li>Rights Owner Program</li><li>Tell us what you think</li></ul></div>
  <div class="fcol" style="left:959px;top:40px"><h4>Help &amp; Contact</h4><ul><li>Resolution Center</li><li>Seller Information Center</li><li>Contact us</li></ul>
    <h4 style="margin-top:30px">Community</h4><ul><li>Announcements</li><li>Answer center</li><li>Discussion boards</li><li>Giving Works</li><li>Celebrity</li><li>Groups</li><li>Top shared picks</li></ul></div>
</footer>
<p class="copyright">Copyright © 2019 Company Name. All Rights Reserved</p>
<div class="connect"><span>Stay Connected</span><b style="background:#3b5998"></b><b style="background:#1da1f2"></b><b style="background:#dd4b39"></b><b style="background:#0077b5"></b></div>

</body>
</html>
```